Zestora - Landing Page

Need a landing page for a journal app. The app is based on a retrospective board, where each journal entry is split into 3 sections: "What went well", "What Didn't Go Well" and "Things To Try".
The landing page should match the style of all modern web application landing pages. Think Brint, Tivalo, Mirvane. I've included screenshots of the app.
One feature that I want to highlight that is not ready yet, is an AI coach. It will offer insights based on the history of the user's journal entries
1 page

```html
<!DOCTYPE html>
<html lang="en">
<head>
<meta charset="utf-8">
<title>Zestora – Journal your way forward</title>
<link href="https://fonts.googleapis.com/css2?family=Roboto:wght@400;500;700;900&display=swap" rel="stylesheet">
<style>
:root{
  --blue:#0d5db8;
  --blue-dark:#0a4b96;
  --ink:#111827;
  --text:#4b5563;
  --muted:#6b7280;
  --line:#e5e7eb;
  --hero-bg:#f4f6fd;
  --soft-blue:#eaf4fb;
  --navy:#1f2a44;
  --green:#3fb871;
  --red:#e5484d;
}
*{box-sizing:border-box;margin:0;padding:0}
html,body{width:1200px;height:3848px;overflow:hidden}
body{font-family:"Roboto",Arial,sans-serif;color:var(--ink);background:#fff;position:relative}
.abs{position:absolute}
a{color:inherit;text-decoration:none}
.btn{position:absolute;display:flex;align-items:center;justify-content:center;gap:8px;border-radius:30px;font-weight:500;font-size:15px}
.btn-solid{background:var(--blue);color:#fff}
.btn-outline{border:2px solid var(--blue);color:var(--blue);background:#fff}
.chev{width:7px;height:7px;border-right:1.8px solid currentColor;border-top:1.8px solid currentColor;transform:rotate(45deg);display:inline-block}

/* header + hero */
.hero-bg{left:0;top:0;width:1200px;height:768px;background:var(--hero-bg)}
.brand{left:142px;top:28px;font-size:24px;font-weight:900;letter-spacing:1px}
.nav{left:351px;top:31px;display:flex;font-size:14px;color:#222}
.nav a{margin-right:27px}
.nav .active{color:var(--blue);border-bottom:1.5px solid var(--blue);padding-bottom:2px}
.search{left:911px;top:34px}
.login{left:956px;top:21px;width:99px;height:39px;font-size:15px}
.hero-title{left:0;width:1200px;top:108px;text-align:center;font-size:37px;font-weight:500}
.hero-sub{left:320px;width:560px;top:170px;text-align:center;font-size:16px;line-height:29px;color:#222}
.demo{left:447px;top:260px;width:136px;height:46px}
.getstarted{left:593px;top:260px;width:159px;height:46px}
.tip{font-size:13px;color:#333}
.feature-dot{border-radius:50%;background:var(--blue);display:flex;align-items:center;justify-content:center;box-shadow:0 0 0 7px rgba(13,93,184,.12)}

/* laptop */
.laptop{left:287px;top:353px;width:626px;height:415px;background:#111;border-radius:20px 20px 0 0}
.laptop-base{left:229px;top:768px;width:738px;height:19px;background:linear-gradient(#d9dbe0,#9ea2aa);border-radius:0 0 30px 30px}
.screen{left:297px;top:366px;width:605px;height:381px;background:#fff;overflow:hidden}
.sidebar{left:0;top:0;width:21px;height:100%;background:var(--navy)}
.sb-i{position:absolute;left:6px;width:9px;height:6px;background:#8793ad;border-radius:1px}
.entry-h{font-size:10px;font-weight:700}
.entry-d{font-size:7px;color:#444}
.tag{font-size:6px;background:var(--green);color:#fff;border-radius:6px;padding:1px 6px}
.col{position:absolute;border:1px solid var(--line);background:#fff}
.col h6{font-size:6px;font-weight:500;padding:6px 8px;border-bottom:1px solid var(--line)}
.toolbar{font-size:5px;color:#555;margin:5px 8px 0;border:1px solid var(--line);border-bottom:none;padding:3px 4px;letter-spacing:1px}
.editor{margin:0 8px;border:1px solid var(--line);padding:5px 6px;font-size:6.4px;line-height:8.4px;color:#333}
.editor li{margin-left:6px}

.msgs{left:902px;top:420px;width:262px;height:237px;background:#fff;border:1px solid #eee;box-shadow:0 6px 24px rgba(20,40,90,.12);padding:14px 16px}
.msgs-h{font-size:10px;font-weight:700;display:flex;align-items:center;gap:8px}
.msgs-h span{font-size:6px;color:var(--red);font-weight:400}
.msg{display:flex;gap:8px;margin-top:15px;position:relative}
.avatar{width:20px;height:20px;border-radius:50%;background:#a8978a;flex:none}
.msg b{font-size:7px;display:block}
.msg p{font-size:6.2px;color:var(--muted)}
.msg i{position:absolute;right:0;top:0;font-style:normal;font-size:6px;color:var(--muted)}

/* trusted */
.trusted{left:0;width:1200px;top:852px;text-align:center;font-size:16px;color:var(--text)}
.logo-box{top:902px;width:218px;height:74px;background:#fff;box-shadow:0 4px 16px rgba(0,0,0,.1);display:flex;align-items:center;justify-content:center;gap:10px;font-size:22px;font-weight:500;color:#333}
.logo-box i{width:26px;height:26px;border-radius:50%;background:#333;display:block}
.arrow-btn{top:922px;width:32px;height:32px;border-radius:50%;background:#fff;box-shadow:0 2px 8px rgba(0,0,0,.18);display:flex;align-items:center;justify-content:center}

/* section two */
.shot-frame{left:134px;top:1079px;width:482px;height:360px;background:#e8e8ea}
.shot{left:146px;top:1095px;width:459px;height:329px;background:#fff;box-shadow:0 4px 14px rgba(0,0,0,.18);overflow:hidden}
.rocket{left:342px;top:1032px;width:90px;height:90px;border-radius:50%;background:var(--blue);border:6px solid #fff;box-shadow:0 4px 16px rgba(0,0,0,.2);display:flex;align-items:center;justify-content:center}
.checkcard{left:191px;top:1386px;width:223px;height:116px;background:#fff;border:1px solid #ddd;box-shadow:0 4px 14px rgba(0,0,0,.12);padding:20px 0 0 28px}
.checkcard li{list-style:none;font-size:12px;color:#444;display:flex;align-items:center;gap:7px;margin-bottom:11px}
.tick{width:12px;height:12px;border-radius:50%;background:var(--blue);position:relative;flex:none}
.tick::after{content:"";position:absolute;left:4px;top:2px;width:3px;height:6px;border:solid #fff;border-width:0 1.5px 1.5px 0;transform:rotate(45deg)}
.h2{font-size:33px;font-weight:500;line-height:48px}
.para{font-size:13.5px;line-height:24px;color:var(--text)}
.ticks li{list-style:none;display:flex;align-items:center;gap:14px;font-size:13.5px;color:var(--text);margin-bottom:11px}

/* band */
.band{left:0;top:1573px;width:1200px;height:253px;background:linear-gradient(110deg,#1568bd,#1b78c8 50%,#1464b8)}
.band h2{position:absolute;top:62px;width:100%;text-align:center;color:#fff;font-size:32px;font-weight:500}
.band .btn{top:141px;height:39px;font-size:14px}
.btn-white{background:#fff;color:var(--blue)}
.btn-ghost{border:1.5px solid #fff;color:#fff}

/* solutions */
.center-title{left:0;width:1200px;text-align:center}
.tabs{left:338px;top:1991px;width:524px;height:66px;border:1.5px solid #cfd3da;border-radius:34px;background:#fff}
.tab{position:absolute;top:10px;height:44px;border-radius:24px;background:#f1f2f4;display:flex;align-items:center;gap:10px;padding:0 20px;font-size:17px;color:#333}
.tab.on{background:var(--blue);color:#fff}
.role-card{top:2114px;width:217px;height:371px;background:#fff;border-radius:14px;box-shadow:0 6px 24px rgba(20,40,90,.10);padding:36px 18px 0 18px}
.role-card h3{font-size:17px;font-weight:500;margin-bottom:15px}
.role-card p{font-size:13.5px;line-height:24px;color:var(--muted)}
.role-card .btn{position:relative;border-radius:4px;width:128px;height:39px;margin:18px 0 0 3px;font-size:14px}
.role-card h4{font-size:15px;font-weight:500;margin:20px 0 19px 5px}
.role-card li{list-style:none;display:flex;align-items:center;gap:7px;font-size:11.5px;color:var(--muted);margin:0 0 14px 5px}

/* fastest */
.shot2-frame{left:605px;top:2579px;width:460px;height:360px;background:#e8e8ea}
.shot2{left:615px;top:2595px;width:440px;height:329px;background:#fff;box-shadow:0 4px 14px rgba(0,0,0,.18);overflow:hidden}
.log{position:absolute;left:55px;font-size:5.4px;line-height:7px;color:#333;border:1px solid var(--line);width:370px;padding:6px 8px}
.log b{font-size:6px}

/* core */
.core-bg{left:0;top:3036px;width:1200px;height:463px;background:var(--soft-blue)}
.photo{left:143px;top:3116px;width:380px;height:329px;border-radius:18px;background:linear-gradient(135deg,#2a78c6,#0b57ad)}

/* footer */
.fh{font-size:17px;font-weight:500;color:#222}
.flinks li{list-style:none;font-size:12.5px;color:#333;display:flex;align-items:center;gap:12px;margin-bottom:9.7px}
.dchev{color:var(--blue);font-size:10px;letter-spacing:-2px}
.field{left:862px;width:190px;border:1px solid #dde0e5;border-radius:3px;font-size:9px;color:#999;padding:6px 7px}
.social{width:27px;height:27px;border-radius:50%;border:1.5px solid var(--blue);background:#fff}
.social.on{background:var(--blue)}
</style>
</head>
<body>

<!-- HEADER & HERO -->
<div class="abs hero-bg"></div>
<div class="abs brand">ZESTORA</div>
<nav class="abs nav">
  <a class="active">Home</a><a>About</a><a>Features</a><a>Resources</a><a>Pricing</a><a>Solutions</a><a>Contact</a>
</nav>
<svg class="abs search" width="13" height="13" viewBox="0 0 13 13"><circle cx="5.5" cy="5.5" r="4" fill="none" stroke="#111" stroke-width="2"/><path d="M8.5 8.5l3.5 3.5" stroke="#111" stroke-width="2"/></svg>
<a class="btn btn-solid login">Login
  <svg width="10" height="11" viewBox="0 0 10 11"><rect x="0" y="4.5" width="10" height="6.5" rx="1" fill="#fff"/><path d="M2.5 4.5V3a2.5 2.5 0 015 0v1.5" fill="none" stroke="#fff" stroke-width="1.5"/></svg></a>

<h1 class="abs hero-title">Organize Your Work And Life, Finally.</h1>
<p class="abs hero-sub">Lorem ipsum dolor sit amet, consectetur adipiscing elit, sed do eiusmod tempor incididunt ut labore et dolore magna aliqua.</p>
<a class="btn btn-solid demo">Demo
  <svg width="13" height="13" viewBox="0 0 13 13"><circle cx="6.5" cy="6.5" r="6.5" fill="#fff"/><path d="M5 4l4 2.5L5 9z" fill="#0d5db8"/></svg></a>
<a class="btn btn-outline getstarted">Get Started <span class="chev"></span></a>

<div class="abs tip" style="left:88px;top:231px">Less than 5 minutes to set up</div>
<div class="abs feature-dot" style="left:136px;top:259px;width:80px;height:80px">
  <svg width="40" height="36" viewBox="0 0 40 36" fill="none" stroke="#fff" stroke-width="1.8"><rect x="2" y="2" width="36" height="26" rx="2"/><path d="M2 8h36M14 34h12M20 28v6"/><circle cx="20" cy="18" r="5"/></svg>
</div>
<div class="abs feature-dot" style="left:120px;top:401px;width:80px;height:80px">
  <svg width="40" height="36" viewBox="0 0 40 36" fill="none" stroke="#fff" stroke-width="1.8"><circle cx="12" cy="9" r="5"/><circle cx="28" cy="9" r="5"/><path d="M3 26c0-6 4-9 9-9s9 3 9 9M19 26c0-6 4-9 9-9s9 3 9 9"/></svg>
</div>
<div class="abs tip" style="left:54px;top:503px;width:150px;text-align:right;line-height:23px">Auto-engage and follow<br>up with visitors</div>

<div class="abs laptop"></div>
<div class="abs laptop-base"></div>
<div class="abs screen">
  <div class="abs sidebar">
    <span class="sb-i" style="top:8px;background:#6bc26b"></span>
    <span class="sb-i" style="top:54px"></span><span class="sb-i" style="top:66px"></span><span class="sb-i" style="top:78px"></span>
    <span class="sb-i" style="top:345px;border-radius:50%;height:9px"></span>
  </div>
  <div class="abs entry-h" style="left:66px;top:30px">Entry</div>
  <div class="abs entry-d" style="left:68px;top:53px">▦ Thu Aug 22 2024 ⌄</div>
  <div class="abs tag" style="left:152px;top:52px">Save</div>
  <div class="col" style="left:70px;top:78px;width:148px;height:261px">
    <h6>What Went Well?</h6>
    <div class="toolbar">Normal ⌄ B I U S M<br>≣ ≣ ⊞ ⊟ &nbsp;T</div>
    <div class="editor" style="height:198px"><ul>
      <li>Completed all scheduled workouts this week.</li>
      <li>Increased bench press weight by 10 pounds.</li>
      <li>Maintained consistent energy levels throughout sessions.</li></ul></div>
  </div>
  <div class="col" style="left:242px;top:78px;width:147px;height:261px">
    <h6>What Didn't Go Well?</h6>
    <div class="toolbar">Normal ⌄ B I U S M<br>≣ ≣ ⊞ ⊟ &nbsp;T</div>
    <div class="editor" style="height:198px"><ul>
      <li>Struggled with form on deadlifts, leading to lower back discomfort.</li>
      <li>Missed two stretching sessions after workouts.</li>
      <li>Skipped meal prep, resulting in inconsistent nutrition.</li></ul></div>
  </div>
  <div class="col" style="left:414px;top:78px;width:145px;height:261px">
    <h6>Things To Try</h6>
    <div class="toolbar">Normal ⌄ B I U S M<br>≣ ≣ ⊞ ⊟ &nbsp;T</div>
    <div class="editor" style="height:198px"><ul>
      <li>Focus on deadlift form by lowering the weight and reviewing proper technique.</li>
      <li>Set reminders for post-workout stretching to prevent muscle tightness.</li>
      <li>Dedicate Sunday evenings to meal prep to ensure a balanced diet.</li></ul></div>
  </div>
</div>

<div class="abs msgs">
  <div class="msgs-h">Messages <span>● 2 Unread Messages</span><span style="margin-left:auto;color:#222;font-size:10px">›</span></div>
  <div class="msg"><div class="avatar"></div><div><b>Mara Lindqvist <span style="color:var(--red)">●</span></b><p>Hi guys, I have some update related top</p></div><i>1m</i></div>
  <div class="msg"><div class="avatar"></div><div><b>Tomas Reyne <span style="color:var(--red)">●</span></b><p>I need to talk about the previous MoM...</p></div><i>47m</i></div>
  <div class="msg"><div class="avatar"></div><div><b>Ilan Petrov</b><p>The potential raising for company A is...</p></div><i>2h</i></div>
  <div class="msg"><div class="avatar"></div><div><b>Nora Vance</b><p>The potential raising for company A is...</p></div><i>7h</i></div>
</div>

<!-- TRUSTED -->
<p class="abs trusted">Trusted By 225,000+ Customers, From Startups To Enterprises</p>
<div class="abs arrow-btn" style="left:78px"><svg width="8" height="10"><path d="M7 0v10L0 5z" fill="#222"/></svg></div>
<div class="abs logo-box" style="left:142px"><i></i>Velmora</div>
<div class="abs logo-box" style="left:374px"><i></i>Quintra</div>
<div class="abs logo-box" style="left:605px"><i></i>Orbisol</div>
<div class="abs logo-box" style="left:837px"><i></i>Kadenz</div>
<div class="abs arrow-btn" style="left:1088px"><svg width="8" height="10"><path d="M1 0v10l7-5z" fill="#222"/></svg></div>

<!-- MOVE FASTER -->
<div class="abs shot-frame"></div>
<div class="abs shot">
  <div class="abs sidebar" style="left:8px;top:28px;width:14px;height:290px">
    <span class="sb-i" style="left:3px;width:7px;top:5px;background:#6bc26b"></span>
    <span class="sb-i" style="left:3px;width:7px;top:30px"></span><span class="sb-i" style="left:3px;width:7px;top:40px"></span><span class="sb-i" style="left:3px;width:7px;top:50px"></span>
  </div>
  <div class="abs entry-h" style="left:55px;top:36px;font-size:7px">Entry</div>
  <div class="abs entry-d" style="left:56px;top:53px;font-size:5px">▦ Wed Aug 21 2024 ⌄</div>
  <div class="abs tag" style="left:118px;top:52px;background:var(--navy);font-size:4.5px">Default journal</div>
  <div class="col" style="left:58px;top:73px;width:110px;height:195px"><h6 style="font-size:4.5px;padding:4px">What Went Well?</h6><div class="toolbar" style="font-size:4px;margin:4px 5px 0">Normal ⌄ B I U S M<br>≣ ≣ ⊞ ⊟ T</div><div class="editor" style="margin:0 5px;height:150px"></div></div>
  <div class="col" style="left:186px;top:73px;width:110px;height:195px"><h6 style="font-size:4.5px;padding:4px">What Didn't Go Well?</h6><div class="toolbar" style="font-size:4px;margin:4px 5px 0">Normal ⌄ B I U S M<br>≣ ≣ ⊞ ⊟ T</div><div class="editor" style="margin:0 5px;height:150px"></div></div>
  <div class="col" style="left:313px;top:73px;width:110px;height:195px"><h6 style="font-size:4.5px;padding:4px">Things To Try</h6><div class="toolbar" style="font-size:4px;margin:4px 5px 0">Normal ⌄ B I U S M<br>≣ ≣ ⊞ ⊟ T</div><div class="editor" style="margin:0 5px;height:150px"></div></div>
</div>
<div class="abs rocket">
  <svg width="36" height="40" viewBox="0 0 36 40" fill="none" stroke="#fff" stroke-width="1.8"><path d="M18 2c6 6 8 14 6 24H12C10 16 12 8 18 2z"/><circle cx="18" cy="14" r="3"/><path d="M12 20l-6 6 1 5 5-3M24 20l6 6-1 5-5-3M15 30l3 7 3-7"/></svg>
</div>
<ul class="abs checkcard">
  <li><span class="tick"></span>Sed ut perspiciatis unde omnis</li>
  <li><span class="tick"></span>Sed ut perspiciatis unde omnis</li>
  <li><span class="tick"></span>Sed ut perspiciatis unde omnis</li>
</ul>
<h2 class="abs h2" style="left:686px;top:1088px">Move Faster With Your<br>Tools In One Place</h2>
<p class="abs para" style="left:686px;top:1192px;width:385px">Lorem ipsum dolor sit amet, consectetur adipiscing elit, sed do eiusmod tempor incididunt ut labore et dolore magna aliqua. Ut enim ad minim veniam, quis nostrud.</p>
<ul class="abs ticks" style="left:686px;top:1277px">
  <li><span class="tick"></span>Lorem ipsum dolor sit ame</li>
  <li><span class="tick"></span>Lorem ipsum dolor sit ame</li>
  <li><span class="tick"></span>Lorem ipsum dolor sit ame</li>
</ul>
<a class="btn btn-solid" style="left:687px;top:1379px;width:129px;height:39px;font-size:14px">Learn More <span class="chev"></span></a>

<!-- AI COACH BAND -->
<section class="abs band">
  <h2>One Features Ready, Is An Ai Coaching</h2>
  <a class="btn btn-white" style="left:403px;width:225px">Meet Brint for Enterprise <span class="chev"></span></a>
  <a class="btn btn-ghost" style="left:644px;width:151px">Talk To Sales <span class="chev"></span></a>
</section>

<!-- SOLUTIONS -->
<h2 class="abs center-title h2" style="top:1890px">A Solution For Every Business</h2>
<p class="abs center-title para" style="top:1943px">Lorem ipsum dolor sit amet, consectetur adipiscing.</p>
<div class="abs tabs">
  <div class="tab on" style="left:10px">
    <svg width="30" height="28" viewBox="0 0 30 28" fill="none" stroke="#fff" stroke-width="1.6"><circle cx="11" cy="8" r="5"/><path d="M2 26c0-6 4-10 9-10 3 0 5 1 7 3"/><circle cx="22" cy="20" r="5"/><path d="M22 17v3l2 1"/></svg>By Role</div>
  <div class="tab" style="left:178px">
    <svg width="28" height="28" viewBox="0 0 28 28" fill="none" stroke="#333" stroke-width="1.5"><circle cx="12" cy="16" r="5"/><circle cx="12" cy="16" r="9" stroke-dasharray="3 2"/><circle cx="22" cy="7" r="4"/></svg>By Industry</div>
  <div class="tab" style="left:369px">
    <svg width="26" height="26" viewBox="0 0 26 26" fill="none" stroke="#333" stroke-width="1.5"><rect x="2" y="2" width="22" height="22" rx="2"/><path d="M9 17l8-8M12 9h5v5M14 17H9v-5"/></svg>By Size</div>
</div>

<div class="abs role-card" style="left:145px">
  <h3>Business Professional</h3>
  <p>Lorem ipsum dolor sit amet, consectetur adipiscing elit, sed do eiusmod tempor.</p>
  <a class="btn btn-solid">Learn More <span class="chev"></span></a>
  <h4>Popular Features</h4>
  <ul><li><span class="tick"></span>Lorem ipsum dolor sit ame</li><li><span class="tick"></span>Lorem ipsum dolor sit ame</li><li><span class="tick"></span>Lorem ipsum dolor sit ame</li></ul>
</div>
<div class="abs role-card" style="left:376px">
  <h3>Procurement Dirctor</h3>
  <p>Lorem ipsum dolor sit amet, consectetur adipiscing elit, sed do eiusmod tempor.</p>
  <a class="btn btn-solid">Learn More <span class="chev"></span></a>
  <h4>Popular Features</h4>
  <ul><li><span class="tick"></span>Lorem ipsum dolor sit ame</li><li><span class="tick"></span>Lorem ipsum dolor sit ame</li><li><span class="tick"></span>Lorem ipsum dolor sit ame</li></ul>
</div>
<div class="abs role-card" style="left:609px">
  <h3>Student/Professor</h3>
  <p>Lorem ipsum dolor sit amet, consectetur adipiscing elit, sed do eiusmod tempor.</p>
  <a class="btn btn-solid">Learn More <span class="chev"></span></a>
  <h4>Popular Features</h4>
  <ul><li><span class="tick"></span>Lorem ipsum dolor sit ame</li><li><span class="tick"></span>Lorem ipsum dolor sit ame</li><li><span class="tick"></span>Lorem ipsum dolor sit ame</li></ul>
</div>
<div class="abs role-card" style="left:841px">
  <h3>Principal/Team Mgr</h3>
  <p>Lorem ipsum dolor sit amet, consectetur adipiscing elit, sed do eiusmod tempor.</p>
  <a class="btn btn-solid">Learn More <span class="chev"></span></a>
  <h4>Popular Features</h4>
  <ul><li><span class="tick"></span>Lorem ipsum dolor sit ame</li><li><span class="tick"></span>Lorem ipsum dolor sit ame</li><li><span class="tick"></span>Lorem ipsum dolor sit ame</li></ul>
</div>

<!-- FASTEST WAY -->
<h2 class="abs h2" style="left:143px;top:2604px">The Fastest Way To Get<br>Tasks Out Of Your Head</h2>
<p class="abs para" style="left:143px;top:2715px;width:386px">Lorem ipsum dolor sit amet, consectetur adipiscing elit, sed do eiusmod tempor incididunt ut labore et dolore magna aliqua. Ut enim ad minim veniam, quis nostrud.</p>
<p class="abs para" style="left:143px;top:2791px;width:386px">Duis aute irure dolor in reprehenderit in voluptate velit esse cillum dolore eu fugiat nulla pariatur.</p>
<a class="btn btn-solid" style="left:143px;top:2864px;width:127px;height:39px;font-size:14px">Learn More <span class="chev"></span></a>

<div class="abs shot2-frame"></div>
<div class="abs shot2">
  <div class="abs sidebar" style="left:5px;top:35px;width:14px;height:285px">
    <span class="sb-i" style="left:3px;width:7px;top:5px;background:#6bc26b"></span>
    <span class="sb-i" style="left:3px;width:7px;top:25px"></span><span class="sb-i" style="left:3px;width:7px;top:35px"></span><span class="sb-i" style="left:3px;width:7px;top:45px"></span>
  </div>
  <div class="abs" style="left:55px;top:58px;font-size:5px;border:1px solid var(--line);padding:2px 5px">+ Add New</div>
  <div class="abs tag" style="left:400px;top:56px;font-size:4.5px">Save</div>
  <div class="log" style="top:85px;height:170px">
    <b>Thu Aug 22 2024</b><br>What Went Well<br>
    Completed all scheduled workouts this week.<br>Increased bench press weight by 10 pounds.<br>Maintained consistent energy levels throughout sessions.<br>
    What Didn't Go Well<br>Struggled with form on deadlifts, leading to lower back discomfort.<br>Missed two stretching sessions after workouts.<br>Skipped meal prep, resulting in inconsistent nutrition.<br>
    Things To Try<br>Focus on deadlift form by lowering the weight and reviewing proper technique.<br>Set reminders for post-workout stretching to prevent muscle tightness.<br>Dedicate Sunday evenings to meal prep to ensure a balanced diet.
  </div>
  <div class="log" style="top:265px;height:40px">
    <b>Tue Aug 20 2024</b><br>What Went Well<br>Achieved a personal best in squats, adding 15 pounds.<br>Stayed hydrated through long training days.
  </div>
</div>

<!-- CORE SOLUTIONS -->
<div class="abs core-bg"></div>
<div class="abs photo" role="img" aria-label="Photo of a smiling man in a plaid shirt working on a laptop"></div>
<h2 class="abs h2" style="left:648px;top:3115px">Core Solutions That Span<br>AcrossYour Business.</h2>
<p class="abs para" style="left:648px;top:3218px;width:412px">Lorem ipsum dolor sit amet, consectetur adipiscing elit, sed do eiusmod tempor incididunt ut labore et dolore magna aliqua. Ut enim ad minim veniam, quis nostrud. Duis aute irure dolor in reprehenderit in voluptate velit esse cillum dolore eu fugiat nulla pariatur. Excepteur sint occaecat cupidatat non proident, sunt in culpa</p>
<a class="btn btn-solid" style="left:647px;top:3370px;width:126px;height:39px;font-size:14px">Get Started <span class="chev"></span></a>

<!-- FOOTER -->
<div class="abs fh" style="left:142px;top:3559px">Quick Links</div>
<ul class="abs flinks" style="left:142px;top:3597px">
  <li><span class="dchev">»</span>Home</li><li><span class="dchev">»</span>About</li><li><span class="dchev">»</span>Features</li><li><span class="dchev">»</span>Resources</li><li><span class="dchev">»</span>Pricing</li><li><span class="dchev">»</span>Solutions</li><li><span class="dchev">»</span>Contact</li>
</ul>
<div class="abs fh" style="left:362px;top:3559px">Product Suite</div>
<ul class="abs flinks" style="left:362px;top:3597px">
  <li><span class="dchev">»</span>How It Works</li><li><span class="dchev">»</span>For Teams</li><li><span class="dchev">»</span>Pricing</li><li><span class="dchev">»</span>Accessibility</li>
</ul>
<div class="abs fh" style="left:362px;top:3707px">Follow Us</div>
<div class="abs" style="left:362px;top:3740px;display:flex;gap:10px">
  <span class="social" aria-label="Social profile"></span><span class="social on" aria-label="Social profile"></span><span class="social" aria-label="Social profile"></span><span class="social" aria-label="Social profile"></span>
</div>
<div class="abs fh" style="left:596px;top:3559px">Resources</div>
<ul class="abs flinks" style="left:596px;top:3597px">
  <li><span class="dchev">»</span>Download Apps</li><li><span class="dchev">»</span>Help Center</li><li><span class="dchev">»</span>Productivity Methods</li><li><span class="dchev">»</span>Integrations</li><li><span class="dchev">»</span>Channel Partners</li><li><span class="dchev">»</span>Developer API</li><li><span class="dchev">»</span>Status</li>
</ul>
<div class="abs fh" style="left:862px;top:3562px">Connect</div>
<div class="abs field" style="top:3601px;height:30px">Name*</div>
<div class="abs field" style="top:3638px;height:30px">Email*</div>
<div class="abs field" style="top:3674px;height:39px">Comment*</div>
<a class="btn btn-solid" style="left:862px;top:3725px;width:135px;height:39px;border-radius:3px;font-size:14px">Submit Now</a>
<div class="abs" style="left:142px;top:3790px;width:914px;height:1px;background:var(--line)"></div>
<p class="abs center-title" style="top:3818px;font-size:12px;color:#444">© 2024 Zestora &nbsp;|&nbsp; All Rights Reserved</p>

</body>
</html>
```